Business card design for a dynamic IT consulting company

We need a business card design for a young firm, specialized in the Telecommunications/Consulting industry. The name of the company is Quindor and Partners Business Consulting Ltd. (Short name: Quindor and Partnes)
Quindor = solve read reverse, so we aim to be uncomplicated and solution-oriented. The small pipe in our logo is also related to the word solve. So we need a new business card design, which is simple, eye catching and something non traditional (I would probably prefer a square shaped design rather than a rectangle, but open for suggestions). Attached our logo.

Target Market(s)

Usually our customers are Tier1 Telecoms providers (Q-Netra, Palorix, etc) and their executives.

Industry/Entity Type

Business

Contact Information for Business Card

Name: Bence Tolnavari
Email: b.tolnavari@quindor.hu
Web: www.quindor.hu
Mobile: +36 30 518 2769
Title: Managing Director

Optional:
Company name: Quindor and Partners Ltd.
Address: 1087 Budapest, Tolvenka str. 28/C, Hungary

Font styles to use
Other font styles liked:
• helveticaneue_medium, Prime Regular are used now.

Colors

Designer to choose colors to be used in the design.

Requirements
Must have
• I would like to have a 2 sided design.
Nice to have
• I thought if we make the logo a bit bigger (without the company name), that could go to the back with the company name below. I though, if the pipe in the logo is somehow touchable on the business card, would be nice and unique.

```html
<!DOCTYPE html>
<html lang="en">
<head>
<meta charset="utf-8">
<title>Quindor and Partners – Business Card</title>
<link href="https://fonts.googleapis.com/css2?family=Source+Sans+3:wght@300;400;600&display=swap" rel="stylesheet">
<style>
  :root {
    --backdrop: #3a3a3a;
    --card: #141414;
    --card-panel: #1b1b1b;
    --magenta: #c22d9a;
    --cyan: #1ea6e0;
    --ink: #f2f2f2;
    --muted: #d6d6d6;
    --mark-grey: #8a8a8a;
  }
  * { box-sizing: border-box; margin: 0; padding: 0; }
  html, body { width: 1200px; height: 900px; overflow: hidden; }
  body {
    background: var(--backdrop);
    font-family: "Source Sans 3", "Helvetica Neue", Arial, sans-serif;
    position: relative;
  }
  .card {
    position: absolute;
    top: 290px;
    width: 520px;
    height: 320px;
    border-radius: 22px;
    background: var(--card);
    overflow: hidden;
  }
  .card--front { left: 60px; }
  .card--back { left: 620px; display: flex; align-items: center; justify-content: center; }

  .front-brand {
    position: absolute;
    left: 0; top: 0;
    width: 240px; height: 100%;
    display: flex; align-items: center; justify-content: center; gap: 10px;
  }
  .brand-square { width: 14px; height: 14px; background: var(--cyan); }
  .brand-name { font-weight: 400; font-size: 34px; color: var(--magenta); letter-spacing: 0.5px; }

  .front-details {
    position: absolute;
    left: 240px; top: 0;
    width: 280px; height: 100%;
    background: var(--card-panel);
    padding: 70px 0 0 30px;
    color: var(--ink);
  }
  .person-name { font-size: 19px; font-weight: 600; line-height: 1.1; }
  .person-name .surname { color: var(--magenta); }
  .person-title { font-size: 13px; color: var(--muted); margin-top: 2px; }
  .company-address { font-size: 13px; line-height: 1.35; color: var(--muted); margin-top: 22px; }
  .contact-list { list-style: none; margin-top: 20px; }
  .contact-list li { display: flex; align-items: center; gap: 10px; font-size: 13px; line-height: 1.55; color: var(--ink); }
  .contact-list svg { width: 11px; height: 11px; flex: none; fill: var(--magenta); }

  .back-brand {
    display: flex; align-items: center; gap: 14px;
  }
  .back-brand .brand-square { width: 18px; height: 18px; background: var(--magenta); }
  .back-brand .brand-name { font-size: 40px; font-weight: 300; color: var(--mark-grey); }
</style>
</head>
<body>
  <section class="card card--front" aria-label="Business card front">
    <div class="front-brand">
      <span class="brand-square"></span>
      <span class="brand-name">Quindor</span>
    </div>
    <div class="front-details">
      <p class="person-name">Bence <span class="surname">Tolnavari</span></p>
      <p class="person-title">Managing Director</p>
      <p class="company-address">Quindor and Partners Ltd.<br>1087 Budapest, Tolvenka str.<br>28/C, Hungary</p>
      <ul class="contact-list">
        <li><svg viewBox="0 0 12 12" aria-hidden="true"><path d="M2.5 0.5 4.5 2.5 3.4 4.1c.8 1.8 2.2 3.2 4.5 4.5L9.5 7.5l2 2-1.5 2C5 11 1 7 .5 2z"/></svg>+36 30 518 2769</li>
        <li><svg viewBox="0 0 12 12" aria-hidden="true"><path d="M0 2h12v8H0zM1 3v.4l5 3.3 5-3.3V3z"/></svg>b.tolnavari@quindor.hu</li>
        <li><svg viewBox="0 0 12 12" aria-hidden="true"><circle cx="6" cy="6" r="6"/></svg>www.quindor.hu</li>
      </ul>
    </div>
  </section>

  <section class="card card--back" aria-label="Business card back">
    <div class="back-brand">
      <span class="brand-square"></span>
      <span class="brand-name">Quindor &amp; Partners</span>
    </div>
  </section>
</body>
</html>
```